English and Spanish Language School Needs a Business Card

Need a business card design a startup company called Maribel Language School. The company will offer English and Spanish conversational level courses designed to make the learner feel comfortable with grammar and vocabulary. We would like to see a logo with some colour that should communicate learning, growth.

Target Market(s)

Consumers and businesses

Industry/Entity Type

Education

Contact Information for Business Card

TBD

Font styles to use
Serif

Requirements
Must have
• Include the following
• Logo
• Name
• Title
• Cellphone Number
• Office Phone number
• Email address
• Office Address

```html
<!DOCTYPE html>
<html lang="en">
<head>
<meta charset="utf-8">
<title>Maribel Language School – Business Card</title>
<link rel="stylesheet" href="https://fonts.googleapis.com/css2?family=Tinos:wght@400;700&family=Open+Sans:wght@400;600&display=swap">
<style>
  :root {
    --red: #d7202f;
    --red-dark: #b8192a;
    --teal: #17b3b6;
    --white: #ffffff;
    --paper: #f4f4f2;
    --stage: #e9e6e1;
  }
  * { margin: 0; padding: 0; box-sizing: border-box; }
  html, body { width: 1200px; height: 780px; overflow: hidden; }
  body { background: var(--stage); position: relative; font-family: "Tinos", serif; }

  .card {
    position: absolute;
    top: 240px;
    width: 520px;
    height: 297px;
    border-radius: 16px;
    overflow: hidden;
    box-shadow: 0 10px 26px rgba(0,0,0,0.18);
  }
  .card--front { left: 50px; background: var(--red); }
  .card--back  {
    left: 630px;
    background: radial-gradient(ellipse at 45% 40%, #dd2634 0%, var(--red) 55%, var(--red-dark) 100%);
  }

  .front-shapes { position: absolute; inset: 0; width: 100%; height: 100%; }

  .brand { position: absolute; color: var(--red); font-family: "Tinos", serif; font-weight: 700; line-height: 1; }
  .card--front .brand { left: 30px; top: 36px; }
  .brand__name { font-size: 60px; letter-spacing: -1px; display: block; }
  .brand__sub { font-size: 20px; display: block; margin-top: 4px; margin-left: 3px; color: var(--teal); font-weight: 400; }
  .card--back .brand { color: var(--white); left: 0; right: 0; top: 92px; text-align: center; }
  .card--back .brand__name { font-size: 84px; }
  .card--back .brand__sub { font-size: 24px; margin-left: 0; color: var(--white); }

  .address {
    position: absolute; right: 24px; top: 184px;
    color: var(--white); text-align: right; font-style: normal;
    font-size: 14px; line-height: 1.35;
  }

  .contact { position: absolute; left: 30px; bottom: 12px; color: var(--white); }
  .contact__name { font-size: 16px; font-weight: 700; letter-spacing: 0.5px; line-height: 1.1; }
  .contact__title { font-size: 12px; margin-bottom: 4px; }
  .contact__row { display: flex; align-items: center; gap: 7px; font-size: 13px; line-height: 1.5; }
  .contact__row--mail { font-family: "Open Sans", sans-serif; font-size: 12px; }
  .icon { width: 12px; height: 12px; flex: none; }
</style>
</head>
<body>

  <section class="card card--front" aria-label="Business card front">
    <svg class="front-shapes" viewBox="0 0 520 297" preserveAspectRatio="none" aria-hidden="true">
      <path d="M0,0 H520 V52 C442,72 402,132 322,162 C232,196 110,182 0,182 Z" fill="var(--teal)"/>
      <path d="M0,0 H520 V44 C440,64 400,124 320,154 C230,188 110,174 0,174 Z" fill="var(--white)"/>
      <path d="M0,0 H520 V40 C440,60 400,120 320,150 C230,184 110,170 0,170 Z" fill="var(--paper)"/>
    </svg>

    <div class="brand">
      <span class="brand__name">Maribel</span>
      <span class="brand__sub">Language School</span>
    </div>

    <address class="address">
      48 Alder Lane, 2nd Ste<br>
      Linden Grove, Texas 1234
    </address>

    <div class="contact">
      <p class="contact__name">DANIEL REYES</p>
      <p class="contact__title">Manager</p>
      <p class="contact__row">
        <svg class="icon" viewBox="0 0 14 14" aria-hidden="true"><rect width="14" height="14" rx="2" fill="#fff"/><rect x="3" y="3" width="8" height="8" rx="1" fill="none" stroke="var(--red)" stroke-width="1.3"/><path d="M4.5 6h5M4.5 8h5" stroke="var(--red)" stroke-width="1"/></svg>
        555 210 4387
      </p>
      <p class="contact__row">
        <svg class="icon" viewBox="0 0 14 14" aria-hidden="true"><rect width="14" height="14" rx="2" fill="#fff"/><path d="M3.5 4c0 3.5 3 6.5 6.5 6.5l1-1.6-2-1-1 .8c-1-.5-1.7-1.2-2.2-2.2l.8-1-1-2z" fill="var(--red)"/></svg>
        555 210 4388
      </p>
      <p class="contact__row contact__row--mail">
        <svg class="icon" viewBox="0 0 14 14" aria-hidden="true"><rect width="14" height="14" rx="2" fill="#fff"/><rect x="2.5" y="4" width="9" height="6.5" fill="none" stroke="var(--red)" stroke-width="1.2"/><path d="M2.5 4l4.5 3.5L11.5 4" fill="none" stroke="var(--red)" stroke-width="1.2"/></svg>
        hello@maribelschool.com
      </p>
    </div>
  </section>

  <section class="card card--back" aria-label="Business card back">
    <div class="brand">
      <span class="brand__name">Maribel</span>
      <span class="brand__sub">Language School</span>
    </div>
  </section>

</body>
</html>
```